Letter and Envelope Design For Harborline Realty

Please design a letter and an envelope incorporating our logo (See Attached). We are also launched a business card contest. Since we want them to match, please feel free to submit a design for both the business card and also the letter design and envelope.

Requirements
Must have
• The envelope, the letter and the business cards must match somehow connecting the designs. We want them to have something that holds them together besides the logo.

```html
<!DOCTYPE html>
<html lang="en">
<head>
<meta charset="utf-8">
<title>Harborline Realty Stationery</title>
<link href="https://fonts.googleapis.com/css2?family=Montserrat:wght@600&family=Source+Sans+3:wght@400;600;700&display=swap" rel="stylesheet">
<style>
:root{
  --blue:#0b1fa3;
  --grey:#5b5b5d;
  --paper:#f5f5f5;
  --ink:#3a3a3a;
  --muted:#6d6d6d;
  --stage:#dedede;
}
*{box-sizing:border-box;margin:0;padding:0}
html,body{width:1200px;height:825px;overflow:hidden}
body{background:var(--stage);font-family:"Source Sans 3",sans-serif;color:var(--ink);position:relative}
.sheet{position:absolute;background:var(--paper);overflow:hidden}
.band{position:absolute;left:0;bottom:0;width:100%}
.brand{display:flex;flex-direction:column;align-items:center;gap:5px;position:absolute;text-align:center}
.brand-dot{border:2px solid var(--blue);border-radius:50%;flex:none}
.brand-name{font-family:"Montserrat",sans-serif;font-weight:600;color:var(--blue);letter-spacing:1.5px;text-transform:uppercase;line-height:1.25;white-space:nowrap}
.sender{position:absolute;display:flex;gap:8px;font-size:6.5px;line-height:10px;color:var(--muted)}
.sender-company{font-weight:700;color:var(--blue)}
.sender-lines{border-left:1px solid #999;padding-left:6px}
.sender-lines span{display:flex;align-items:center;gap:4px}
.icon{width:5px;height:5px;background:var(--blue);border-radius:1px;display:inline-block}
/* letter */
.letter{left:80px;top:84px;width:464px;height:656px}
.letter .brand{left:38px;top:26px;width:108px}
.letter .brand-dot{width:32px;height:32px}
.letter .brand-name{font-size:10px}
.letter .sender{left:244px;top:42px}
.salutation{position:absolute;left:37px;top:149px;font-size:7.5px;font-weight:700}
.body-copy{position:absolute;left:37px;top:172px;width:389px;font-size:9.6px;line-height:12.1px;text-align:justify}
.body-copy p{margin-bottom:12px}
.signature{position:absolute;left:37px;top:396px;width:90px;height:42px;background:linear-gradient(90deg,#e6e6e6,#dadada)}
/* cards */
.card-front{left:646px;top:108px;width:197px;height:112px}
.card-front .brand{left:6px;top:30px;width:86px;gap:4px}
.card-front .brand-dot{width:24px;height:24px}
.card-front .brand-name{font-size:7px;letter-spacing:1px}
.card-divider{position:absolute;left:98px;top:28px;width:1px;height:56px;background:#aaa}
.card-details{position:absolute;left:107px;top:27px;font-size:5.4px;line-height:7px;color:var(--muted)}
.card-name{font-size:7px;font-weight:700;color:var(--blue);line-height:9px}
.card-gap{height:5px}
.card-back{left:865px;top:108px;width:196px;height:112px;background:var(--blue);color:#fff}
.card-back .brand-name{position:absolute;top:42px;width:100%;text-align:center;color:#fff;font-size:10px}
.card-web{position:absolute;bottom:6px;width:100%;display:flex;justify-content:center;align-items:center;gap:5px;font-size:5.4px}
.card-web i{width:18px;height:1px;background:#fff;display:block}
/* envelopes */
.envelope{left:583px;top:246px;width:532px;height:231px}
.envelope .brand{left:36px;top:19px;width:108px}
.envelope .brand-dot{width:32px;height:32px}
.envelope .brand-name{font-size:10px}
.envelope .sender{left:313px;top:34px}
.address-box{position:absolute;left:34px;top:131px;width:205px;height:60px;background:#fafafa;border:1px solid #e3e3e3;border-radius:4px;padding:14px 8px 0}
.address-box i{display:block;border-top:1px dashed #bbb;margin-bottom:11px}
.envelope-back{left:583px;top:504px;width:532px;height:232px;background:#f7f7f7}
.flap{position:absolute;left:0;top:0;width:100%;height:58px;border:1px solid #e0e0e0;border-top:none;border-radius:0 0 14px 14px;background:var(--paper)}
</style>
</head>
<body>

<section class="sheet letter">
  <div class="brand"><span class="brand-dot"></span><span class="brand-name">Harborline<br>Realty</span></div>
  <div class="sender">
    <div><div class="sender-company">Harborline Realty</div>PO Box 418, Bayview Street,<br>Port Town, Zip Code - 00000</div>
    <div class="sender-lines"><span><i class="icon"></i>555-214-7730</span><span><i class="icon"></i>hello@harborlinerealty.com</span><span><i class="icon"></i>hello@harborlinerealty.com</span></div>
  </div>
  <div class="salutation">Dear Mr. Carter,</div>
  <div class="body-copy">
    <p>Lorem ipsum is simply dummy text of the printing and typesetting industry. Lorem ipsum has been the industry's standard dummy text ever since the 1500s, when an unknown printer took a galley of type and scrambled it to make a type specimen book. It has survived not only five centuries, but also the leap into electronic typesetting, remaining essentially unchanged.</p>
    <p>The standard chunk of Lorem ipsum used since the 1500s is reproduced below for those interested. Sections 1.10.32 and 1.10.33 of the classic Latin text are also reproduced in their exact original form, accompanied by English versions taken from a later translation of the work.</p>
    <p>Lorem ipsum is simply dummy text of the printing and typesetting industry. Lorem ipsum has been the industry's standard dummy text ever since the 1500s, when an unknown printer took a galley of type and scrambled it to make a type specimen book. It has survived not only five centuries, but also the leap into electronic typesetting, remaining essentially unchanged. It was popularised in the</p>
  </div>
  <div class="signature" role="img" aria-label="Handwritten signature of the sender"></div>
  <svg class="band" height="8" viewBox="0 0 464 8" preserveAspectRatio="none">
    <polygon points="0,0 222,0 232,8 0,8" fill="var(--blue)"/>
    <polygon points="226,0 464,0 464,8 236,8" fill="var(--grey)"/>
  </svg>
</section>

<section class="sheet card-front">
  <div class="brand"><span class="brand-dot"></span><span class="brand-name">Harborline<br>Realty</span></div>
  <div class="card-divider"></div>
  <div class="card-details">
    <div class="card-name">DANIEL REYES</div>Director
    <div class="card-gap"></div>PO Box 418, Bayview Street,<br>Port Town, Zip Code - 00000
    <div class="card-gap"></div>(555) 301-4472<br>hello@harborlinerealty.com<br>www.harborlinerealty.com
  </div>
  <svg class="band" height="5" viewBox="0 0 197 5" preserveAspectRatio="none">
    <polygon points="0,0 94,0 99,5 0,5" fill="var(--blue)"/>
    <polygon points="97,0 197,0 197,5 102,5" fill="var(--grey)"/>
  </svg>
</section>

<section class="sheet card-back">
  <div class="brand-name">Harborline<br>Realty</div>
  <div class="card-web"><i></i>www.harborlinerealty.com<i></i></div>
</section>

<section class="sheet envelope">
  <div class="brand"><span class="brand-dot"></span><span class="brand-name">Harborline<br>Realty</span></div>
  <div class="sender">
    <div><div class="sender-company">Harborline Realty</div>PO Box 418, Bayview Street,<br>Port Town, Zip Code - 00000</div>
    <div class="sender-lines"><span><i class="icon"></i>555-214-7730</span><span><i class="icon"></i>hello@harborlinerealty.com</span><span><i class="icon"></i>hello@harborlinerealty.com</span></div>
  </div>
  <div class="address-box"><i></i><i></i><i></i><i></i></div>
  <svg class="band" height="7" viewBox="0 0 532 7" preserveAspectRatio="none">
    <polygon points="0,0 254,0 264,7 0,7" fill="var(--blue)"/>
    <polygon points="258,0 532,0 532,7 268,7" fill="var(--grey)"/>
  </svg>
</section>

<section class="sheet envelope-back">
  <div class="flap"></div>
</section>

</body>
</html>
```